Marlowe Crest Realty business card design

Looking for an upscale and clean business card design and updated logo. I sell to a very high-end south Florida real estate market.
Target Market(s)
High-end real estate in south Florida real estate market
Industry/Entity Type
Real Estate Agent
Contact Information for Business Card
Marlowe Crest Realty, Inc
738 West Pinecrest Ave, Suite 410/510, Fort Lauderdale, FL 33308
Gary Whitlock - Broker/Owner
954-327-8846 Direct
garyshomes@quellmail.com
Website: DwellTarrowBay.com
Font styles to use
Other font styles liked:
- Copperplate Gothic, Georgia, etc.
Requirements
Must have
- My photo, company name, my name and title, all info stated in Details above
Nice to have
- Luxury home design element, waterfront

```html
<!DOCTYPE html>
<html lang="en">
<head>
<meta charset="utf-8">
<title>Marlowe Crest Realty – Business Card</title>
<link rel="stylesheet" href="https://fonts.googleapis.com/css2?family=Sorts+Mill+Goudy&family=Michroma&family=Open+Sans:wght@400;600&display=swap">
<style>
  :root {
    --backdrop: #2f2f31;
    --card: #ffffff;
    --ink: #1d1d1f;
    --sun: #f2c230;
    --night: #050505;
    --edge: #1f2d7a;
  }
  * { box-sizing: border-box; margin: 0; padding: 0; }
  html, body { width: 1200px; height: 1073px; overflow: hidden; }
  body {
    background: var(--backdrop);
    font-family: "Open Sans", sans-serif;
    color: var(--ink);
    position: relative;
  }
  .card {
    position: absolute;
    left: 280px;
    width: 640px;
    height: 366px;
    background: var(--card);
    border-radius: 24px;
    overflow: hidden;
    box-shadow: 0 6px 0 var(--edge), 0 18px 40px rgba(0,0,0,.45);
  }
  .card--front { top: 100px; }
  .card--back { top: 598px; }

  .brand {
    display: flex;
    align-items: center;
    gap: 14px;
    font-family: "Sorts Mill Goudy", serif;
    color: var(--ink);
  }
  .brand__dot {
    width: 56px; height: 56px;
    border-radius: 50%;
    background: var(--sun);
    flex: none;
  }
  .card--front .brand {
    position: absolute;
    left: 50%; top: 50%;
    transform: translate(-50%, -50%);
    font-size: 27px;
    white-space: nowrap;
  }
  .card--back .brand {
    position: absolute;
    left: 38px; top: 62px;
    font-size: 21px;
  }
  .card--back .brand__dot { width: 44px; height: 44px; }

  .wave { position: absolute; inset: 0; width: 100%; height: 100%; }

  .holder {
    position: absolute;
    left: 372px; top: 128px;
  }
  .holder__name {
    font-family: "Michroma", sans-serif;
    color: var(--sun);
    font-size: 17px;
    letter-spacing: 4px;
  }
  .holder__title { font-size: 8px; margin-top: 1px; color: #333; }

  .contacts {
    position: absolute;
    left: 372px; top: 172px;
    list-style: none;
    font-size: 15px;
    line-height: 24px;
  }
  .contacts li { display: flex; align-items: center; gap: 8px; }
  .contacts svg { width: 15px; height: 15px; flex: none; }

  .address {
    position: absolute;
    left: 340px; top: 316px;
    color: #fff;
    font-size: 12px;
    line-height: 16px;
    font-style: normal;
  }
</style>
</head>
<body>
  <section class="card card--front" aria-label="Card front">
    <div class="brand"><span class="brand__dot"></span>Marlowe Crest Realty, Inc</div>
  </section>

  <section class="card card--back" aria-label="Card back">
    <svg class="wave" viewBox="0 0 640 366" preserveAspectRatio="none" aria-hidden="true">
      <path d="M0 184 C180 222 380 262 510 280 C570 288 615 320 640 350 L640 366 L0 366 Z" fill="var(--sun)"/>
      <path d="M0 214 C180 250 380 290 500 305 C560 313 600 340 620 366 L0 366 Z" fill="var(--night)" stroke="#fff" stroke-width="3"/>
    </svg>

    <div class="brand"><span class="brand__dot"></span>Marlowe Crest Realty, Inc</div>

    <div class="holder">
      <div class="holder__name">JONAH PELL</div>
      <div class="holder__title">CEO/Managing Director</div>
    </div>

    <ul class="contacts">
      <li>
        <svg viewBox="0 0 24 24"><path d="M6.6 10.8a15 15 0 0 0 6.6 6.6l2.2-2.2c.3-.3.7-.4 1-.2 1.1.4 2.3.6 3.6.6.6 0 1 .4 1 1V20c0 .6-.4 1-1 1A17 17 0 0 1 3 4c0-.6.4-1 1-1h3.5c.6 0 1 .4 1 1 0 1.3.2 2.5.6 3.6.1.3 0 .7-.2 1z" fill="var(--sun)"/></svg>
        214-555-0174
      </li>
      <li>
        <svg viewBox="0 0 24 24"><path d="M6 3h12v5H6z M4 9h16a2 2 0 0 1 2 2v6h-4v4H6v-4H2v-6a2 2 0 0 1 2-2z M8 15v4h8v-4z" fill="var(--sun)"/></svg>
        214-555-0174
      </li>
      <li>
        <svg viewBox="0 0 24 24"><path d="M2 5h20v14H2z" fill="var(--sun)"/><path d="M2 5l10 8 10-8" fill="none" stroke="#fff" stroke-width="1.6"/></svg>
        jonahpell@quellmail.com
      </li>
    </ul>

    <address class="address">
      412 Harlow Avenue NW<br>
      Suite 400, Grand Ledge MI 48837
    </address>
  </section>
</body>
</html>
```